Borvik Media - Amazing Homepage

We would like to build an amazing homepage for our site. We will need it built in HTM5, so it works across devices and would like it to parallax scroll , so it looks amazing.
We are a digital media agency, that has recently launched. Our old site is self build through one of the standard web build sites. We will be hosting our new site independently.
This is our old site - www.borvik-media.example
The new site only really needs one scrolling page to explain what we do and have our contact details at the bottom.
We have a place to host it, once designed. So we can share with the final design for you to upload.
Attached are:
Brief
Logos and artwork
Our PowerPoint template to give you an idea of colours

```html
<!DOCTYPE html>
<html lang="en">
<head>
<meta charset="utf-8">
<title>Borvik Media – Homepage</title>
<link href="https://fonts.googleapis.com/css2?family=Roboto:wght@300;400;500;700&family=Roboto+Slab:wght@700&display=swap" rel="stylesheet">
<style>
:root{
  --maroon:#8c1d3b;
  --maroon-dark:#74172f;
  --ink:#333;
  --muted:#666;
  --band:#e6e6e8;
  --panel:#ececec;
  --white:#fff;
}
*{margin:0;padding:0;box-sizing:border-box}
html,body{width:1200px;height:2764px;overflow:hidden}
body{position:relative;background:var(--white);font-family:'Roboto',Arial,sans-serif;color:var(--ink)}
.abs{position:absolute}
.site-header{left:0;top:0;width:1200px;height:132px;background:var(--white)}
.brand{left:118px;top:20px;display:flex;align-items:center;gap:16px}
.brand-mark{width:64px;height:64px;border-radius:50%;background:var(--maroon)}
.brand-name{font-weight:700;font-size:26px;color:var(--maroon);letter-spacing:1px}
.brand-tag{font-size:15px;color:var(--muted);margin-top:2px}
.main-nav{right:118px;top:56px;display:flex;gap:36px;font-size:15px;font-weight:500;color:var(--ink)}
.hero{left:0;top:132px;width:1200px;height:648px;background:linear-gradient(135deg,#cfd3d6 0%,#9aa0a5 45%,#5e646a 100%)}
.caption{background:rgba(40,40,40,.85);color:#fff;font-size:18px;font-weight:500;padding:16px 26px;left:50%;transform:translateX(-50%);white-space:nowrap}
.scroll-btn{width:52px;height:52px;border-radius:50%;background:#fff;left:574px;display:flex;align-items:center;justify-content:center;box-shadow:0 0 0 2px #ccc}
.scroll-btn.dark{background:#555;box-shadow:none}
.clarity-title{left:118px;top:820px;font-family:'Roboto Slab',Georgia,serif;font-size:20px;font-weight:700;color:var(--maroon)}
.clarity-list{left:128px;top:860px;list-style:none;font-size:15px;line-height:32px;color:var(--ink)}
.clarity-list li::before{content:"";display:inline-block;width:9px;height:9px;background:var(--maroon);margin-right:18px;vertical-align:middle}
.quote-panel{left:300px;top:1028px;width:600px;height:116px;background:var(--panel);text-align:center;font-size:20px;font-weight:300;line-height:34px;padding-top:24px;color:#444;white-space:nowrap}
.marbles{left:0;top:1220px;width:1200px;height:320px;background:linear-gradient(90deg,#6b8fb5,#c8a74a 30%,#b0453b 55%,#4f7c5a 80%,#8aa3c6)}
.coup{left:0;width:1200px;text-align:center;color:var(--maroon);font-size:24px;font-weight:300;line-height:32px}
.kart{left:208px;top:1640px;width:872px;height:196px;background:linear-gradient(180deg,#e9eaec 0%,#c9ccd0 55%,#b23b34 100%)}
.services{left:0;top:2000px;width:1200px;height:300px;background:var(--band);text-align:center}
.services p{font-size:19px;font-weight:300;line-height:32px;color:#444}
.service-row{display:flex;justify-content:center;gap:54px;margin-top:30px}
.service{width:96px;display:flex;flex-direction:column;align-items:center;gap:10px;font-size:13px;font-weight:500;color:#444}
.service-icon{width:54px;height:54px;border-radius:50%;background:#fff;border:2px solid #aaa;display:flex;align-items:center;justify-content:center}
.services p.board{margin-top:18px;font-size:18px}
.results{left:0;top:2344px;width:1200px;text-align:center;font-size:19px;font-weight:300;line-height:30px;color:#444}
.clients{left:0;top:2430px;width:1200px;display:flex;justify-content:center;gap:46px}
.client{display:flex;align-items:center;gap:8px;font-size:20px;font-weight:700;color:var(--maroon)}
.client i{width:18px;height:18px;background:var(--maroon);display:block}
.site-footer{left:0;top:2528px;width:1200px;height:236px;background:var(--maroon-dark);color:#f1dce2}
.address{left:118px;top:28px;font-size:14px;line-height:24px}
.follow{right:118px;top:28px;font-size:14px;line-height:24px;text-align:right}
.copyright{left:0;width:1200px;bottom:22px;text-align:center;font-size:12px}
</style>
</head>
<body>
<header class="site-header abs">
  <div class="brand abs"><span class="brand-mark"></span><div><div class="brand-name">BORVIK</div><div class="brand-tag">we make amazing</div></div></div>
  <nav class="main-nav abs"><span>HOME</span><span>ABOUT US</span><span>WHAT WE CAN OFFER</span><span>CONTACT US</span></nav>
</header>

<section class="hero abs" role="img" aria-label="Photo of a businesswoman holding a tablet over a world map backdrop">
  <div class="caption abs" style="top:280px">GOT THE FEELING YOUR DIGITAL MARKETING JUST ISN'T QUITE 'THERE'?</div>
  <div class="scroll-btn abs" style="top:556px"><svg width="20" height="20" viewBox="0 0 20 20"><path d="M10 3v13M4 10l6 6 6-6" stroke="#555" stroke-width="2.5" fill="none"/></svg></div>
</section>

<h2 class="clarity-title abs">WE KEEP FIGHTING TO GIVE YOU CLARITY BY</h2>
<ul class="clarity-list abs">
  <li>Creating a singular view of your digital eco system</li>
  <li>Reviewing how and why your money is being spent where it is</li>
  <li>Profiling your customers. Why doesn't have 1000's of different customers with different motivations, interests and value to the brand?</li>
  <li>Finding the best digital channels to communicate with them</li>
</ul>
<div class="quote-panel abs">Because everything is changing every day...exciting isn't it!<br>Never stop, never settle, always improve. Be amazing</div>
<div class="scroll-btn abs" style="top:1160px"><svg width="20" height="20" viewBox="0 0 20 20"><path d="M10 3v13M4 10l6 6 6-6" stroke="#555" stroke-width="2.5" fill="none"/></svg></div>

<section class="marbles abs" role="img" aria-label="Photo of a pile of colourful glass marbles">
  <div class="caption abs" style="top:128px;background:rgba(60,60,60,.7);font-weight:300;font-size:19px">Every client deserves amazing work, regardless of the brand; it's all real money</div>
</section>

<p class="coup abs" style="top:1564px">It's time to start a coup...there are too many large agency networks, too few agencies<br>being transparent, too many putting quality of work second to income</p>

<div class="kart abs" role="img" aria-label="Photo of a child driving a red toy racing kart"></div>
<div class="scroll-btn dark abs" style="top:1856px"><svg width="20" height="20" viewBox="0 0 20 20"><path d="M10 3v13M4 10l6 6 6-6" stroke="#fff" stroke-width="2.5" fill="none"/></svg></div>

<p class="coup abs" style="top:1946px">Well, a very quiet coup.</p>

<section class="services abs">
  <p style="padding-top:28px">We've yet to come across a client that wants to shrink...making us specialists in delivering growth!<br>We've been optimising our digital knowledge for over 20 years and we genuinely know what we are talking about</p>
  <div class="service-row">
    <div class="service"><span class="service-icon"><svg width="26" height="26" viewBox="0 0 26 26"><path d="M8 4l12 10-6 1 3 7-3 1-3-7-4 4z" fill="#444"/></svg></span>PPC</div>
    <div class="service"><span class="service-icon"><svg width="26" height="26" viewBox="0 0 26 26"><circle cx="13" cy="13" r="6" fill="none" stroke="#444" stroke-width="3"/><path d="M13 2v5M13 19v5M2 13h5M19 13h5" stroke="#444" stroke-width="3"/></svg></span>SEO</div>
    <div class="service"><span class="service-icon"><svg width="26" height="26" viewBox="0 0 26 26"><rect x="3" y="5" width="20" height="13" fill="none" stroke="#444" stroke-width="2.5"/><path d="M9 22h8M13 18v4" stroke="#444" stroke-width="2.5"/></svg></span>DISPLAY</div>
    <div class="service"><span class="service-icon"><svg width="26" height="26" viewBox="0 0 26 26"><path d="M4 20V12M10 20V7M16 20v-5M22 20V4" stroke="#444" stroke-width="3"/></svg></span>PAID SOCIAL</div>
    <div class="service"><span class="service-icon"><svg width="26" height="26" viewBox="0 0 26 26"><ellipse cx="13" cy="6" rx="8" ry="3" fill="#444"/><path d="M5 6v14c0 4 16 4 16 0V6" fill="none" stroke="#444" stroke-width="2.5"/><path d="M5 13c0 4 16 4 16 0" fill="none" stroke="#444" stroke-width="2.5"/></svg></span>DATA MANAGEMENT</div>
    <div class="service"><span class="service-icon"><svg width="26" height="26" viewBox="0 0 26 26"><rect x="6" y="4" width="14" height="18" fill="none" stroke="#444" stroke-width="2.5"/><path d="M9 10h8M9 14h8M9 18h5" stroke="#444" stroke-width="2"/></svg></span>ATTRIBUTION</div>
  </div>
  <p class="board">Operating at board level in top 10 digital agencies</p>
</section>

<p class="results abs">Happily, we smash it for all our clients, with an average of 35% improvement in performance<br>within the first quarter of working with us</p>
<div class="clients abs">
  <span class="client"><i></i>Hadley</span>
  <span class="client"><i></i>Rovana</span>
  <span class="client"><i></i>Softel</span>
  <span class="client"><i></i>Stagepass</span>
  <span class="client"><i></i>Pelora</span>
</div>

<footer class="site-footer abs">
  <div class="address abs">14 Marlow Street, London, EC1 4QT<br>contact@borvik-media.example</div>
  <div class="follow abs">Follow us on<br>Pagebook · Chirper · Linkline</div>
  <div class="copyright abs">Copyright © 2013 All Rights Reserved</div>
</footer>
</body>
</html>
```